holloway paving service

Needs to have phone number 0418259730 and email markholloway@brightmail.com.au.
ABN 62318470915
name mark holloway

For all your concreting solutions
Excavation
Exposed & colour concrete
House & shed slabs
Driveways
Landing & steps

Contact Information for Business Card

ph 0418259730
email markholloway@brightmail.com.au.
ABN 62318470915
name mark holloway

```html
<!DOCTYPE html>
<html lang="en">
<head>
<meta charset="utf-8">
<title>Holloway Paving Service – Business Card</title>
<link rel="stylesheet" href="https://fonts.googleapis.com/css2?family=Roboto:wght@400;700&family=Montserrat:wght@700&display=swap">
<style>
  :root {
    --page-bg: #e9e6e2;
    --card-light: #dcdcdc;
    --card-light-edge: #c9c9c9;
    --accent: #e0492a;
    --accent-deep: #b8321a;
    --panel-dark: #3b3b3d;
    --panel-dark-edge: #2a2a2c;
    --text-light: #ffffff;
    --text-soft: #e6e6e6;
    --text-dark: #2e2e30;
  }
  * { box-sizing: border-box; margin: 0; padding: 0; }
  html, body {
    width: 1200px; height: 969px; overflow: hidden;
    background: var(--page-bg);
    font-family: "Roboto", Arial, sans-serif;
  }
  .card {
    position: absolute; left: 100px; top: 200px;
    width: 1000px; height: 570px;
    background: linear-gradient(135deg, var(--card-light), var(--card-light-edge));
    box-shadow: 0 10px 30px rgba(0,0,0,0.18);
    overflow: hidden;
  }
  .card-bands { position: absolute; inset: 0; }
  .owner-name {
    position: absolute; left: 52px; top: 66px;
    font-size: 32px; font-weight: 700; color: var(--text-light);
    letter-spacing: 0.5px; text-transform: uppercase;
  }
  .contact-list { position: absolute; left: 54px; top: 128px; list-style: none; }
  .contact-list li {
    display: flex; align-items: center; gap: 14px;
    font-size: 22px; color: var(--text-soft); height: 31px;
  }
  .contact-list svg { width: 20px; height: 20px; fill: var(--text-soft); flex: none; }
  .abn {
    position: absolute; left: 56px; top: 338px;
    font-size: 22px; color: var(--text-soft); letter-spacing: 0.5px;
  }
  .service-list { position: absolute; left: 56px; top: 372px; list-style: none; }
  .service-list li {
    display: flex; align-items: center; gap: 14px;
    font-size: 22px; color: var(--text-soft); height: 30px;
  }
  .service-list li::before {
    content: ""; width: 8px; height: 8px; background: var(--text-soft);
    transform: rotate(45deg); flex: none;
  }
  .brand {
    position: absolute; left: 540px; top: 252px;
    display: flex; align-items: center; gap: 18px;
  }
  .brand-mark { width: 34px; height: 34px; background: var(--accent); flex: none; }
  .brand-rule { width: 3px; height: 86px; background: var(--accent-deep); flex: none; }
  .brand-text { display: flex; flex-direction: column; gap: 6px; }
  .brand-name {
    font-family: "Montserrat", Arial, sans-serif; font-weight: 700;
    font-size: 24px; line-height: 1.15; color: var(--accent);
    text-transform: uppercase; letter-spacing: 0.5px;
  }
  .brand-phone {
    font-family: "Montserrat", Arial, sans-serif; font-weight: 700;
    font-size: 19px; color: var(--text-dark); letter-spacing: 1px;
  }
</style>
</head>
<body>
  <div class="card">
    <svg class="card-bands" viewBox="0 0 1000 570" width="1000" height="570" aria-hidden="true">
      <defs>
        <linearGradient id="accentFill" x1="0" y1="0" x2="1" y2="1">
          <stop offset="0" stop-color="#e85230"/>
          <stop offset="1" stop-color="#c83a1e"/>
        </linearGradient>
        <linearGradient id="darkFill" x1="0" y1="0" x2="1" y2="1">
          <stop offset="0" stop-color="#47474a"/>
          <stop offset="1" stop-color="#2a2a2c"/>
        </linearGradient>
      </defs>
      <polygon points="0,0 580,0 395,272 0,272" fill="url(#accentFill)"/>
      <polygon points="0,282 398,282 610,570 0,570" fill="url(#darkFill)"/>
    </svg>

    <h1 class="owner-name">Mark Holloway</h1>
    <ul class="contact-list">
      <li><svg viewBox="0 0 24 24"><path d="M6.6 10.8a15.1 15.1 0 0 0 6.6 6.6l2.2-2.2a1 1 0 0 1 1-.25 11.4 11.4 0 0 0 3.6.57 1 1 0 0 1 1 1V20a1 1 0 0 1-1 1A17 17 0 0 1 3 4a1 1 0 0 1 1-1h3.5a1 1 0 0 1 1 1c0 1.25.2 2.45.57 3.57a1 1 0 0 1-.25 1z"/></svg>0418259730</li>
      <li><svg viewBox="0 0 24 24"><path d="M2 5h20v14H2z M3 6.5v.6l9 6 9-6v-.6z" fill-rule="evenodd"/></svg>markholloway@brightmail.com.au</li>
      <li><svg viewBox="0 0 24 24"><circle cx="12" cy="12" r="10"/><path d="M12 2v20M2 12h20" stroke="#d4442a" stroke-width="1.6" fill="none"/></svg>www.hollowaypaving.com.au</li>
    </ul>

    <p class="abn">ABN 62318470915</p>
    <ul class="service-list">
      <li>Excavation</li>
      <li>Exposed &amp; colour concrete</li>
      <li>House &amp; shed slabs</li>
      <li>Driveways</li>
      <li>Landing &amp; steps</li>
    </ul>

    <div class="brand">
      <span class="brand-mark"></span>
      <span class="brand-rule"></span>
      <div class="brand-text">
        <span class="brand-name">Holloway Paving<br>Service</span>
        <span class="brand-phone">0418259730</span>
      </div>
    </div>
  </div>
</body>
</html>
```